Harbor Wonder Hour - A magic website for a monthly modern magic show

Looking to build a website to promote my new monthly magic show

Sites like this. https://velvetloftshow.example/ https://sevencuriouscardsnight.example/

Target Market(s)

18-65 year old men and women who enjoy live entertainment especially magic

Industry/Entity Type

Entertainment

Coding

Coded - Design and coding required

Number of Pages Required

3 page

Colors

Designer to choose colors to be used in the design.

Requirements
Must have
• Wanting a wordpress site.
• Contact form, media section for photos and videos to be posted.
• A “reviews/testimonials” section.

```html
<!DOCTYPE html>
<html lang="en">
<head>
<meta charset="utf-8">
<title>Harbor Wonder Hour</title>
<link rel="stylesheet" href="https://fonts.googleapis.com/css2?family=Crimson+Pro:wght@400;500&family=Poppins:wght@400;500&display=swap">
<style>
:root{
  --bg:#141414;
  --bg-deep:#0b0b0b;
  --band:#0e0e0e;
  --gold:#b8924e;
  --gold-soft:#8a6e3c;
  --text:#e9e6e0;
  --muted:#8c8a86;
  --line:#4a4a4a;
}
*{margin:0;padding:0;box-sizing:border-box}
html,body{width:1200px;height:4049px;overflow:hidden}
body{background:linear-gradient(180deg,#121212 0%,var(--bg) 40%,#161616 100%);color:var(--text);font-family:"Crimson Pro",Georgia,serif;position:relative}
h2{font-weight:400}
.abs{position:absolute}
.photo{position:absolute}
.site-header{position:absolute;left:0;top:0;width:1200px;height:110px;z-index:5}
.brand{position:absolute;left:55px;top:41px;font-family:"Poppins",Arial,sans-serif;font-weight:500;font-size:17px;letter-spacing:2px;color:var(--gold);text-transform:uppercase;white-space:nowrap}
.nav{position:absolute;left:0;top:0;width:1200px;height:110px;font-family:"Poppins",Arial,sans-serif;font-size:11px;font-weight:500;color:var(--text)}
.nav span{position:absolute;top:47px;white-space:nowrap;line-height:14px}
.nav-cta{position:absolute;left:1020px;top:43px;font-size:17px;line-height:20px;color:var(--gold);letter-spacing:.3px;white-space:nowrap}
.hero{position:absolute;left:0;top:0;width:1200px;height:809px;background:radial-gradient(ellipse at 60% 35%,#2a2a2a 0%,#151515 45%,#0f0f0f 100%)}
.show-name{position:absolute;left:55px;top:395px;width:240px;font-size:32px;line-height:38px;color:#f1eee8;text-align:center;letter-spacing:1px}
.scroll-down{position:absolute;left:0;width:1200px;top:713px;text-align:center;font-size:11px;letter-spacing:5px;color:var(--gold)}
.dots{position:absolute;left:1138px;top:403px}
.dots i{display:block;width:3px;height:3px;background:#666;margin-bottom:4px}
.dots i.on{background:var(--gold)}
.frame{position:absolute;border:1px solid var(--gold-soft)}
.h2{font-weight:400;color:var(--text)}
.lede{font-size:11.5px;line-height:14.5px;color:#dedbd5}
.more{font-size:12.5px;color:var(--text);display:flex;align-items:center;gap:8px;white-space:nowrap}
.more b{display:inline-block;width:9px;height:9px;border:1px solid var(--gold);position:relative}
.more b::after{content:"";position:absolute;left:2px;top:2px;border-left:3px solid var(--gold);border-top:2px solid transparent;border-bottom:2px solid transparent}
.section-title{position:absolute;left:0;width:1200px;text-align:center;font-size:18px;letter-spacing:.5px;color:var(--text)}
.section-title span{display:inline-flex;align-items:center;gap:12px}
.section-title span::before,.section-title span::after{content:"";width:70px;height:1px;background:var(--gold-soft)}
.media-card{position:absolute;top:1477px;width:358px;height:220px}
.media-card .tag{position:absolute;left:0;width:100%;top:126px;text-align:center;font-size:12px;letter-spacing:2px;color:var(--gold)}
.media-card svg{position:absolute;left:164px;top:92px}
.stars{position:absolute;left:0;width:1200px;top:1866px;text-align:center;color:var(--gold);font-size:12px;letter-spacing:1px}
.quote{position:absolute;left:286px;width:628px;top:1906px;text-align:center;font-size:11.5px;line-height:14.5px;color:#dedbd5}
.reviewer{position:absolute;left:0;width:1200px;top:1953px;text-align:center;font-family:"Poppins",Arial,sans-serif;font-size:16px;color:var(--gold)}
.newsletter{position:absolute;left:0;top:2038px;width:1200px;height:135px;background:var(--band)}
.email-box{position:absolute;left:176px;top:44px;width:518px;height:48px;border:1px solid #3c3c3c;border-radius:4px}
.email-box .ph{position:absolute;left:16px;top:16px;font-family:"Poppins",Arial,sans-serif;font-size:10px;color:#777}
.email-box .div{position:absolute;left:465px;top:12px;width:1px;height:24px;background:#555}
.email-box svg{position:absolute;left:480px;top:15px}
.nl-title{position:absolute;left:724px;top:42px;font-size:17px;display:flex;align-items:center;gap:8px;white-space:nowrap}
.nl-title::after{content:"";width:70px;height:1px;background:var(--gold-soft)}
.nl-text{position:absolute;left:724px;top:66px;width:260px;font-size:11px;line-height:14px;color:#dedbd5}
.event-band{position:absolute;left:0;top:2460px;width:660px;height:242px;background:var(--band)}
.gold-h{position:absolute;font-size:31px;line-height:36px;font-weight:400;color:var(--gold);text-transform:uppercase;white-space:nowrap}
.field{position:absolute;border-bottom:1px solid var(--line);height:20px}
.field span{position:absolute;left:9px;bottom:4px;font-family:"Poppins",Arial,sans-serif;font-size:9px;color:#777}
.site-footer{position:absolute;left:0;top:3959px;width:1200px;height:90px;background:var(--bg-deep)}
.copy{position:absolute;left:0;width:1200px;top:41px;text-align:center;font-family:"Poppins",Arial,sans-serif;font-size:8px;letter-spacing:1px;color:#777}
.social{position:absolute;left:1084px;top:38px;display:flex;gap:6px}
.social i{width:15px;height:15px;border-radius:50%;background:var(--gold)}
</style>
</head>
<body>

<section class="hero">
  <div class="photo" role="img" aria-label="Hand tossing dice in low light" style="left:330px;top:150px;width:620px;height:470px;background:radial-gradient(ellipse at 45% 50%,#4a4a4a 0%,#2c2c2c 40%,rgba(20,20,20,0) 75%)"></div>
  <div class="show-name">Seven Curious Cards</div>
  <div class="dots"><i></i><i></i><i></i><i class="on"></i></div>
  <div class="scroll-down">SCROLL DOWN ↓</div>
</section>

<header class="site-header">
  <div class="brand">Harbor Wonder Hour</div>
  <nav class="nav">
    <span style="left:674px">About</span>
    <span style="left:728px">|</span>
    <span style="left:752px">Reviews</span>
    <span style="left:819px">|</span>
    <span style="left:843px">Photos</span>
    <span style="left:902px">|</span>
    <span style="left:925px">Contact Us</span>
  </nav>
  <div class="nav-cta">BOOK TICKETS</div>
</header>

<section class="about">
  <div class="frame" style="left:-2px;top:812px;width:540px;height:521px"></div>
  <div class="photo" role="img" aria-label="Candlelit magic altar with skull and bottles" style="left:0;top:850px;width:500px;height:446px;background:linear-gradient(135deg,#2f4a2a 0%,#3a3322 40%,#4a3a22 60%,#2a2040 100%)"></div>
  <div class="photo" role="img" aria-label="Spinning playing card in motion" style="left:393px;top:765px;width:250px;height:210px;background:radial-gradient(ellipse at center,#dcdad6 0%,#bdbab5 45%,rgba(180,180,180,0) 72%)"></div>
  <h2 class="h2 abs" style="left:561px;top:988px;font-size:41px;display:flex;align-items:center;gap:12px">About us<span style="width:70px;height:1px;background:var(--gold-soft)"></span></h2>
  <p class="lede abs" style="left:561px;top:1059px;width:548px">Lorem Ipsum is simply dummy text of the printing and typesetting industry. Lorem Ipsum has been the industry's standard dummy text ever since the 1500s, when an unknown printer took a galley of type and scrambled it to make a type specimen book. It has survived not only five centuries, but also the leap into electronic typesetting, remaining essentially unchanged.</p>
  <div class="more abs" style="left:561px;top:1137px">learn more <b></b></div>
</section>

<section class="media">
  <div class="section-title" style="top:1414px"><span>PHOTO VIDEOS</span></div>
  <div class="media-card" style="left:31px">
    <div class="photo" role="img" aria-label="Person in blue hoodie holding a camera" style="left:0;top:0;width:358px;height:220px;background:linear-gradient(135deg,#4a5a5a,#2e4a7a 50%,#6a5040)"></div>
    <svg width="30" height="30" viewBox="0 0 30 30"><circle cx="15" cy="15" r="13" fill="none" stroke="#b8924e" stroke-width="1.5"/><circle cx="14" cy="14" r="5" fill="none" stroke="#b8924e" stroke-width="1.5"/><line x1="18" y1="18" x2="22" y2="22" stroke="#b8924e" stroke-width="1.5"/></svg>
    <div class="tag">View Photo</div>
  </div>
  <div class="media-card" style="left:421px">
    <div class="photo" role="img" aria-label="Playing card held in dark hands" style="left:0;top:0;width:358px;height:220px;background:radial-gradient(ellipse at 50% 40%,#6a5a52,#2a1c1c 70%)"></div>
    <svg width="30" height="30" viewBox="0 0 30 30"><circle cx="15" cy="15" r="13" fill="none" stroke="#b8924e" stroke-width="1.5"/><circle cx="14" cy="14" r="5" fill="none" stroke="#b8924e" stroke-width="1.5"/><line x1="18" y1="18" x2="22" y2="22" stroke="#b8924e" stroke-width="1.5"/></svg>
    <div class="tag">View Photo</div>
  </div>
  <div class="media-card" style="left:811px">
    <div class="photo" role="img" aria-label="Person reading a book outdoors" style="left:0;top:0;width:358px;height:220px;background:linear-gradient(160deg,#3a3f44,#2a4a4a 55%,#3a3a3a)"></div>
    <svg width="30" height="30" viewBox="0 0 30 30"><circle cx="15" cy="15" r="13" fill="none" stroke="#b8924e" stroke-width="1.5"/><path d="M12 9 L21 15 L12 21 Z" fill="none" stroke="#b8924e" stroke-width="1.5"/></svg>
    <div class="tag">Watch Video</div>
  </div>
  <svg class="abs" style="left:572px;top:1726px" width="56" height="16" viewBox="0 0 56 16"><path d="M2 8h18M2 8l6-5M2 8l6 5M36 8h18M54 8l-6-5M54 8l-6 5" stroke="#e9e6e0" stroke-width="1.3" fill="none"/></svg>
</section>

<section class="reviews">
  <div class="section-title" style="top:1817px"><span>REVIEWS TESTIMONIALS</span></div>
  <div class="stars">★★★★★</div>
  <p class="quote">Lorem Ipsum is simply dummy text of the printing and typesetting industry. Lorem Ipsum has been the industry's standard dummy text ever since the 1500s, when an unknown printer took a galley of type and scrambled it to make a type specimen book. It has survived not only five centuries, but also the leap into electronic typesetting, remaining essentially unchanged.</p>
  <div class="reviewer">MARLON T. AVERY</div>
</section>

<section class="newsletter">
  <div class="email-box">
    <span class="ph">enter email here</span>
    <span class="div"></span>
    <svg width="20" height="18" viewBox="0 0 20 18"><path d="M1 8 L19 1 L13 17 L9 10 Z" fill="#b8924e"/></svg>
  </div>
  <div class="nl-title">SUBSCRIBE NEWSLETTER</div>
  <p class="nl-text">Lorem Ipsum is simply dummy text of the printing and typesetting industry.</p>
</section>

<section class="event">
  <div class="frame" style="left:663px;top:2320px;width:540px;height:523px"></div>
  <div class="photo" role="img" aria-label="Audience watching a live magic performance" style="left:699px;top:2364px;width:501px;height:442px;background:linear-gradient(140deg,#3a3a3a,#5a4a3e 45%,#8a6a50 80%,#c9b49a)"></div>
  <div class="event-band"></div>
  <div class="photo" role="img" aria-label="Spinning playing card in motion" style="left:548px;top:2222px;width:260px;height:230px;background:radial-gradient(ellipse at center,#dcdad6 0%,#bdbab5 45%,rgba(180,180,180,0) 72%)"></div>
  <h2 class="h2 abs" style="left:160px;width:456px;top:2502px;font-size:44px;display:flex;align-items:center;justify-content:flex-end;gap:14px;white-space:nowrap"><span style="width:70px;height:1px;background:var(--gold-soft)"></span>Event Title Here</h2>
  <p class="lede abs" style="left:70px;width:546px;top:2573px;text-align:right">Lorem Ipsum is simply dummy text of the printing and typesetting industry. Lorem Ipsum has been the industry's standard dummy text ever since the 1500s, when an unknown printer took a galley of type and scrambled it to make a type specimen book. It has survived not only five centuries, but also the leap into electronic typesetting, remaining essentially unchanged.</p>
  <div class="more abs" style="left:545px;top:2649px">learn more <b></b></div>
  <div class="abs" style="left:535px;top:2732px;display:flex;align-items:center;gap:8px;font-size:12px">
    <svg width="40" height="14" viewBox="0 0 40 14"><path d="M2 7h37M2 7l7-6M2 7l7 6" stroke="#e9e6e0" stroke-width="1.3" fill="none"/></svg>NEXT
  </div>
</section>

<section class="attend">
  <div class="photo" role="img" aria-label="Hands exchanging a playing card at a dinner table" style="left:0;top:2945px;width:680px;height:472px;background:linear-gradient(90deg,#3a3028 0%,#4a3a30 45%,#2a2622 75%,rgba(20,20,20,0) 100%)"></div>
  <h2 class="gold-h" style="left:699px;top:3038px">Are you serious about<br>attending once?</h2>
  <p class="lede abs" style="left:699px;top:3121px;width:400px">Lorem Ipsum is simply dummy text of the printing and typesetting industry. Lorem Ipsum has been the industry's standard dummy text ever since the 1500s, when an unknown printer took a galley of type and scrambled it to make a type specimen book. It has survived not only five centuries, but also the leap into electronic typesetting, remaining essentially unchanged.</p>
  <p class="lede abs" style="left:699px;top:3218px;width:400px">It is a long established fact that a reader will be distracted by the readable content of a page when looking at its layout. The point of using Lorem Ipsum is that it has a more-or-less normal distribution of letters, as opposed to using 'Content here, content here', making it look like readable English.</p>
  <div class="more abs" style="left:697px;top:3296px">Book Tickets <b></b></div>
</section>

<section class="contact">
  <div class="section-title" style="top:3490px"><span>CONTACT US</span></div>
  <div class="field" style="left:118px;top:3567px;width:479px"><span>name</span></div>
  <div class="field" style="left:605px;top:3567px;width:476px"><span>email</span></div>
  <div class="field" style="left:118px;top:3636px;width:963px"><span>subject</span></div>
  <div class="field" style="left:118px;top:3810px;width:963px"><span>message</span></div>
  <div class="more abs" style="left:574px;top:3869px">Submit <b></b></div>
</section>

<footer class="site-footer">
  <div class="copy">MONTHLY MAGIC SHOW COPYRIGHT © 2019</div>
  <div class="social"><i></i><i></i><i></i></div>
</footer>

</body>
</html>
```